Corporate Travel Technology Company needs new Business Card design

We need a new business card design to reflect our re-branded company. Our company is called tolvEn (pronounced tolvenn) and we provide Business Intelligence and mobile travel management solutions for the corporate travel industry. Our multinational customers use our solutions to manage large travel budgets and frequent travellers, as well as to save money and reduce risk. We'd like to see designs that use the blue and green palette as well as our corporate logo (attached below). The design should communicate innovation, insight, forward thinking, contemporary, trusted.

Target Market(s)

Large multinational corporates and Travel Agencies.

Industry/Entity Type

Business

Contact Information for Business Card

Rosalind Mercer
Chief Executive
tolvEn
Phone number - +61 (0)2 8134 2907
Email address - rosalind.mercer@tolven-example.com
Mobile number - +61 (0)438 516 702
www.tolven-example.com

Font styles to use
Other font styles liked:
• Please use font as close to corporate logo as possible

Colors
0255a3
0393ce
00a990
33b8a4
33a6d7
3176b5

Requirements
Must have
• Please include the words;
• Mobile Travel Management
• Accelerating Travel Business Insights
• Use corporate logo - although icon can be stylised if needed

```html
<!DOCTYPE html>
<html lang="en">
<head>
<meta charset="utf-8">
<title>tolvEn Business Card</title>
<link rel="stylesheet" href="https://fonts.googleapis.com/css2?family=Open+Sans:wght@400;600;700&display=swap">
<style>
  :root {
    --backdrop: #eceff1;
    --card: #ffffff;
    --brand-blue: #0393ce;
    --brand-green: #00a990;
    --brand-slate: #3e4f55;
    --ink: #2b2b2b;
    --pattern-blue: #e3f3fb;
    --pattern-green: #e2f5f1;
    --card-shadow: rgba(30, 40, 50, 0.18);
  }
  * { box-sizing: border-box; margin: 0; padding: 0; }
  html, body {
    width: 1200px; height: 900px; overflow: hidden;
    background: var(--backdrop);
    font-family: "Open Sans", Arial, sans-serif;
  }
  .stage { position: relative; width: 1200px; height: 900px; }
  .card {
    position: absolute; width: 520px; height: 318px;
    background: var(--card);
    box-shadow: 0 10px 30px var(--card-shadow);
    overflow: hidden;
  }
  .card--back { left: 50px; top: 291px; }
  .card--front { left: 630px; top: 291px; }

  .card__pattern {
    position: absolute; inset: 0;
    background: linear-gradient(135deg, var(--pattern-blue), #f3fafd 55%, var(--pattern-green));
  }
  .logo {
    position: absolute; display: flex; align-items: center;
    color: var(--brand-slate); font-weight: 400; letter-spacing: -0.5px;
  }
  .logo__dot {
    border-radius: 50%; border: 3px solid var(--brand-blue);
    margin-right: 10px;
  }
  .tagline {
    position: absolute; color: var(--brand-green);
    font-weight: 600; letter-spacing: 0.3px; white-space: nowrap;
  }
  .card--back .logo { right: 26px; bottom: 54px; font-size: 46px; line-height: 1; }
  .card--back .logo__dot { width: 24px; height: 24px; }
  .card--back .tagline { right: 28px; bottom: 28px; font-size: 13px; }

  .card--front .logo { left: 40px; bottom: 64px; font-size: 82px; line-height: 1; }
  .card--front .logo__dot { width: 44px; height: 44px; border-width: 5px; }
  .card--front .tagline { left: 44px; bottom: 30px; font-size: 15px; }

  .contact { position: absolute; left: 268px; top: 30px; width: 240px; }
  .contact__name { color: var(--brand-blue); font-weight: 700; font-size: 19px; line-height: 1.2; }
  .contact__title { color: var(--ink); font-size: 13px; margin-top: 2px; }
  .contact__list { list-style: none; margin-top: 26px; }
  .contact__item {
    display: flex; align-items: center; gap: 8px;
    color: var(--ink); font-size: 12px; line-height: 20px; white-space: nowrap;
  }
  .contact__icon { width: 12px; height: 12px; flex: none; fill: var(--brand-blue); }
</style>
</head>
<body>
<main class="stage">
  <section class="card card--back" aria-label="Business card, back">
    <div class="card__pattern" role="img" aria-label="Faint light-blue and green repeating brand pattern"></div>
    <div class="logo"><span class="logo__dot"></span>tolvEn</div>
    <p class="tagline">Accelerating Travel Business Insights</p>
  </section>

  <section class="card card--front" aria-label="Business card, front">
    <div class="contact">
      <p class="contact__name">Rosalind Mercer</p>
      <p class="contact__title">Chief Executive</p>
      <ul class="contact__list">
        <li class="contact__item">
          <svg class="contact__icon" viewBox="0 0 24 24" aria-hidden="true"><path d="M6.6 10.8a15.1 15.1 0 0 0 6.6 6.6l2.2-2.2c.3-.3.7-.4 1-.2 1.1.4 2.3.6 3.6.6.6 0 1 .4 1 1V20c0 .6-.4 1-1 1A17 17 0 0 1 3 4c0-.6.4-1 1-1h3.5c.6 0 1 .4 1 1 0 1.3.2 2.5.6 3.6.1.3 0 .7-.2 1z"/></svg>
          +61 (0)2 8134 2907
        </li>
        <li class="contact__item">
          <svg class="contact__icon" viewBox="0 0 24 24" aria-hidden="true"><path d="M7 1h10a2 2 0 0 1 2 2v18a2 2 0 0 1-2 2H7a2 2 0 0 1-2-2V3a2 2 0 0 1 2-2zm0 3v14h10V4zm5 15.5a1.2 1.2 0 1 0 0 2.4 1.2 1.2 0 0 0 0-2.4z"/></svg>
          +61 (0)438 516 702
        </li>
        <li class="contact__item">
          <svg class="contact__icon" viewBox="0 0 24 24" aria-hidden="true"><path d="M2 5h20v14H2zm2 2v.5l8 5 8-5V7zm0 2.9V17h16V9.9l-8 5z"/></svg>
          rosalind.mercer@tolven-example.com
        </li>
        <li class="contact__item">
          <svg class="contact__icon" viewBox="0 0 24 24" aria-hidden="true"><path d="M10.6 13.4a1 1 0 0 1 0-1.4l4-4a1 1 0 1 1 1.4 1.4l-4 4a1 1 0 0 1-1.4 0zM8.5 20a4.5 4.5 0 0 1-3.2-7.7l2.5-2.5 1.4 1.4-2.5 2.5a2.5 2.5 0 0 0 3.5 3.5l2.5-2.5 1.4 1.4-2.5 2.5A4.5 4.5 0 0 1 8.5 20zm7.7-5.8-1.4-1.4 2.5-2.5a2.5 2.5 0 0 0-3.5-3.5l-2.5 2.5-1.4-1.4 2.5-2.5a4.5 4.5 0 0 1 6.4 6.4z"/></svg>
          www.tolven-example.com
        </li>
      </ul>
    </div>
    <div class="logo"><span class="logo__dot"></span>tolvEn</div>
    <p class="tagline">Mobile Travel Management</p>
  </section>
</main>
</body>
</html>
```